Psychology service brochure

Marketing brochure for a new psychological counselling service.
Our old brochure was too boring and conservative. We are selling our services to GP's, psychiatrists, other health providers and of course potential clients. We'd really like a professional, elegant look that conveys us to be compassionate and conscientious providers of psychological services.
I have included a copy of our old brochure and a copy of the changes we'd like to the text.
Updates
I have included a photo of myself and my business partner. Only the faces are needed, so backgrounds would need to be edited out.
Hello, in consultation with my business partner, we would like
the use of our photos in the brochure please (with backgrounds edited out)
no stock photos of random people
use of abstract or nature/floral motifs suggestive of tranquillity
regards,
Rosalind
Target Market(s)
General practitioner doctors, potential clients
Industry/Entity Type
Health
Requirements
Must have
- must include BlairMdITC TT- font for the business name
- must include our signature color Pantone 291 (see attached brochure)
- use of the photos of myself and my business partner (with background edited out please)
- keep use of colours to a minimum, 3 colors maximum, one of which must be Pantone 291
- must include changes to the brochure as outlined in the 'Changes to Pamphlet' document.
Nice to have
- an interesting, eye catching layout.
- interesting use of white spaces
- use of subtle abstract or nature/floral related graphics suggestive of tranquillity
Should not have
- should not include our fee
- stock photos of people

```html
<!DOCTYPE html>
<html lang="en">
<head>
<meta charset="utf-8">
<title>Quiet Harbour Counselling – Brochure Inner Spread</title>
<link href="https://fonts.googleapis.com/css2?family=Arimo:ital,wght@0,400;0,700;1,400&display=swap" rel="stylesheet">
<style>
  :root {
    --brand-green: #0d5a13;
    --text-green: #1b6a1f;
    --paper: #ffffff;
    --canvas: #ffffff;
  }
  * { margin: 0; padding: 0; box-sizing: border-box; }
  html, body { width: 1200px; height: 900px; overflow: hidden; background: var(--canvas); }
  body { position: relative; font-family: "Arimo", Arial, sans-serif; color: var(--text-green); }

  .spread-shapes { position: absolute; left: 0; top: 0; }

  .profile-heading, .fee-heading, .body-column, .fee-copy, .bulk-note, .business-name {
    position: absolute;
  }
  .profile-heading {
    left: 144px;
    color: var(--paper);
    font-weight: 700;
    font-size: 14.5px;
    line-height: 20px;
  }
  .profile-heading.first { top: 123px; }
  .profile-heading.second { top: 452px; }

  .body-column {
    width: 266px;
    font-size: 14.1px;
    line-height: 15.3px;
  }
  .body-column p + p { margin-top: 7px; }
  .col-left { left: 144px; }
  .col-right { left: 441px; }
  .first-bio { top: 208px; }
  .second-bio { top: 536px; }

  .fee-heading {
    left: 872px; top: 128px;
    color: var(--paper);
    font-weight: 700;
    font-size: 18.5px;
    letter-spacing: 0.6px;
    word-spacing: 4px;
  }
  .fee-copy {
    left: 874px; top: 178px;
    width: 216px;
    font-size: 14.1px;
    line-height: 15.3px;
  }
  .fee-copy p + p { margin-top: 7px; }

  .bulk-note {
    left: 885px; top: 647px;
    width: 205px;
    color: var(--paper);
    font-style: italic;
    font-size: 14.1px;
    line-height: 18.5px;
  }

  .business-name {
    left: 103px; top: 784px;
    color: var(--brand-green);
    font-size: 26px;
    font-weight: 400;
    white-space: nowrap;
  }
</style>
</head>
<body>

<svg class="spread-shapes" width="1200" height="900" viewBox="0 0 1200 900" aria-hidden="true">
  <rect x="56" y="57" width="1091" height="777" fill="var(--paper)"/>

  <path d="M56 57 H128 V565 Q128 578 114 578 H99 Q85 578 85 592 V834 H56 Z" fill="var(--brand-green)"/>
  <path d="M128 57 H150 V95 Q128 95 128 108 Z" fill="var(--paper)"/>

  <path d="M120 110 H356 Q368 110 368 122 V182 H748 Q753 182 753 186 Q753 191 748 191 H140 Q128 191 128 203 V191 H120 Z" fill="var(--brand-green)"/>

  <path d="M120 428 H128 Q128 441 142 441 H356 Q368 441 368 453 V512 H748 Q753 512 753 516.5 Q753 521 748 521 H140 Q128 521 128 533 V428 Z" fill="var(--brand-green)"/>

  <path d="M787 57 H858 V552 Q858 565 844 565 H829 Q815 565 815 579 V834 H787 Z" fill="var(--brand-green)"/>
  <path d="M858 57 H880 V95 Q858 95 858 108 Z" fill="var(--paper)"/>

  <path d="M850 110 H1087 Q1099 110 1099 122 V152 Q1099 164 1087 164 H872 Q858 164 858 178 V164 H850 Z" fill="var(--brand-green)"/>

  <path d="M872 630 H1147 V737 H872 Q858 737 858 723 V644 Q858 630 872 630 Z" fill="var(--brand-green)"/>
</svg>

<h2 class="profile-heading first">Rosalind Hartley<br>Clinical Psychologist<br>M.Psych (Clin.) MAPS</h2>

<div class="body-column col-left first-bio">
  <p>Rosalind is a Clinical Psychologist with fifteen years of experience providing a range of psychological services to challenging clients within the public mental health sector including forensic, addiction and dual diagnosis services. She has been employed as a Senior Psychologist in this capacity for the last seven years.</p>
  <p>Rosalind is a trained and experienced Cognitive Behavioural Therapist and is skilled in treating individuals and groups with a range of mood disorders including anxiety, depression and panic disorder,</p>
</div>
<div class="body-column col-right first-bio">
  <p>as well as in helping clients to overcome life issues such as grief and loss, stress management and anger management.</p>
  <p>Rosalind trains other mental health clinicians and university students in treatment modalities including Motivational Interviewing and Brief Interventions. She has an interest in brain-based research into neuroplasticity and it’s application to cognitive therapy and change.</p>
</div>

<h2 class="profile-heading second">Imogen Ashcroft<br>Psychologist<br>M.Psych (Clin.) MAPS</h2>

<div class="body-column col-left second-bio">
  <p>Imogen is a Psychologist, and with fifteen years experience working in the public health sector, seven as a Senior Psychologist, she is a highly skilled clinician in the areas of mental health, addiction and dual diagnosis.</p>
  <p>She has more recently specialised in working with adolescents but has significant experience treating adults, both individually and in a variety of group programmes. She has also facilitated numerous training events and mentored clinicians in addressing dual diagnosis issues with their clients.</p>
</div>
<div class="body-column col-right second-bio">
  <p>Imogen primarily utilises a Cognitive Behavioural framework and Motivational Interviewing and has a special interest in working with adolescents who are experiencing developmental difficulties, antenatal and post-natal depression/stress, and parenting issues. Additionally Imogen is skilful working in the areas of grief &amp; loss, life transition and adjustment issues, relationship and interpersonal challenges, and personal development.</p>
</div>

<div class="business-name">Quiet Harbour Counselling</div>

<h2 class="fee-heading">OUR FEE STRUCTURE</h2>
<div class="fee-copy">
  <p>The practice accepts referrals from self-referring individuals, as well as from health professionals such as GPs, Psychiatrists, and Maternal and Child Health Nurses.</p>
  <p>CareShield rebates are available for clients referred for treatment by their GP.</p>
  <p>There are different tiers of rebates for Psychologists under CareShield, and this is dependent on treatment received (individual, group or pregnancy support counselling), and whether you are treated by a Psychologist or a Clinical Psychologist.</p>
  <p>Please contact us directly to further discuss fees for treatment.</p>
  <p>Fees are paid in full at the end of each session, and a receipt is provided which will allow you to obtain your refund at any CareShield office.</p>
</div>

<p class="bulk-note">The practice does not bulk bill at this time, but we anticipate the addition of this facility in the future</p>

</body>
</html>
```